We are a specialised Chartered Accountant recruiting business and we are hosting a Casino Night for newly qualified CAs.1. We need a flyer Designed that will be sent out to all newly qualified CAs with 1. Information about the event and to 2. probe them to attendThe below information to be included:Date : 07th of November 2019 (Thursday)Venue : Copper Lantern Grill Johannesburg | Peltoni Vaal Plaza, 14 Orrin Lane, SandtonArrive : 18: 30 Dress code : Smart Casual / CocktailEntertainment : Drinks & Snacks will be provided RSVP : Movent Representative
Target Market(s)
23 - 27 year olds
Colors
Designer to choose colors to be used in the design.
Requirements
Must have
- The Flyer must have the event Title " Quillfern Staffing Movent Casino Night
- Must have the below details
- Date : 07th of November 2019 (Thursday)
- Venue : Copper Lantern Grill Johannesburg | Peltoni Vaal Plaza, 14 Orrin Lane,
- Sandton
- Arrive : 18: 30
- Dress code : Smart Casual / Cocktail
- Entertainment : Drinks & Snacks will be provided
- RSVP : Movent Representative
Nice to have
- Can use either one of the images we sent through not necessarily both
Should not have
- Must have all the details i have provided about the event.
- Must have a catchy line inviting people to come to the event.

```html
<!DOCTYPE html>
<html lang="en">
<head>
<meta charset="utf-8">
<title>Casino Night Flyer</title>
<link href="https://fonts.googleapis.com/css2?family=Anton&family=Oswald:wght@500&family=Great+Vibes&family=Lato:wght@400&family=Cormorant+Garamond:wght@700&display=swap" rel="stylesheet">
<style>
  :root {
    --ink: #050505;
    --panel: #0d0d0d;
    --band: #151515;
    --gold: #f2b52a;
    --gold-light: #fbe7a1;
    --gold-deep: #c9921d;
    --silver-top: #f4f4f4;
    --silver-bottom: #9a9a9a;
    --white: #ffffff;
    --heart-red: #b3141b;
  }
  html, body {
    margin: 0;
    padding: 0;
    width: 1021px;
    height: 1200px;
    overflow: hidden;
    background: var(--ink);
  }
  .flyer {
    position: relative;
    width: 1021px;
    height: 1200px;
    background: linear-gradient(180deg, var(--ink) 0%, var(--panel) 45%, var(--ink) 100%);
    overflow: hidden;
    font-family: "Lato", sans-serif;
  }
  .suit-scatter {
    position: absolute;
    left: 0; top: 20px;
    width: 1021px; height: 330px;
    background: radial-gradient(ellipse at 50% 35%, rgba(179,20,27,0.55) 0%, rgba(120,10,15,0.35) 40%, rgba(5,5,5,0) 75%);
  }
  .damask-band {
    position: absolute;
    left: 0; top: 557px;
    width: 1021px; height: 256px;
    background: var(--band);
  }
  .gaming-art {
    position: absolute;
    left: 175px; top: 165px;
    width: 673px; height: 355px;
    border-radius: 14px;
    background: radial-gradient(ellipse at 50% 45%, #e8e8e8 0%, #a9a9a9 38%, #3a3a3a 68%, rgba(13,13,13,0) 100%);
  }
  .frame-lines {
    position: absolute;
    left: 0; top: 0;
    width: 1021px; height: 1200px;
  }
  .title-casino {
    position: absolute;
    left: 0; width: 1021px;
    top: 478px;
    text-align: center;
    font-family: "Anton", sans-serif;
    font-size: 178px;
    line-height: 1;
    letter-spacing: 4px;
    background: linear-gradient(180deg, var(--silver-top) 0%, #d9d9d9 45%, var(--silver-bottom) 50%, #c8c8c8 100%);
    -webkit-background-clip: text;
    background-clip: text;
    color: transparent;
    margin: 0;
  }
  .title-night {
    position: absolute;
    left: 20px; width: 1021px;
    top: 606px;
    text-align: center;
    font-family: "Great Vibes", cursive;
    font-size: 118px;
    line-height: 1;
    color: var(--white);
  }
  .event-date {
    position: absolute;
    left: 0; width: 1021px;
    top: 800px;
    text-align: center;
    font-family: "Oswald", sans-serif;
    font-weight: 500;
    font-size: 36px;
    line-height: 44px;
    color: var(--gold);
    margin: 0;
  }
  .rule {
    position: absolute;
    left: 234px;
    width: 558px;
    height: 1px;
    background: var(--gold-light);
  }
  .rule-top { top: 851px; }
  .rule-bottom { top: 938px; }
  .venue {
    position: absolute;
    left: 0; width: 1021px;
    top: 866px;
    text-align: center;
    color: var(--white);
    font-size: 20px;
    line-height: 28px;
    margin: 0;
  }
  .details {
    position: absolute;
    left: 0; width: 1021px;
    top: 959px;
    text-align: center;
    color: var(--gold);
    font-size: 20px;
    line-height: 28px;
    margin: 0;
  }
  .rsvp {
    position: absolute;
    left: 264px; top: 1034px;
    width: 453px; height: 49px;
    border-radius: 25px;
    background: linear-gradient(90deg, var(--gold) 0%, var(--gold-light) 55%, var(--gold-deep) 100%);
    display: flex;
    align-items: center;
    justify-content: center;
    font-family: "Cormorant Garamond", serif;
    font-weight: 700;
    font-size: 27px;
    color: var(--ink);
  }
</style>
</head>
<body>
  <main class="flyer">
    <div class="suit-scatter" role="img" aria-label="Scattered red and black heart, spade and club suit symbols"></div>
    <div class="damask-band" role="img" aria-label="Dark damask pattern band"></div>

    <svg class="frame-lines" viewBox="0 0 1021 1200" aria-hidden="true">
      <defs>
        <linearGradient id="goldStroke" x1="0" y1="0" x2="1" y2="1">
          <stop offset="0" stop-color="#f7c948"/>
          <stop offset="0.5" stop-color="#fbe7a1"/>
          <stop offset="1" stop-color="#d99e22"/>
        </linearGradient>
      </defs>
      <g stroke="url(#goldStroke)" fill="none">
        <!-- diamond diagonals -->
        <path d="M510 0 L0 404 M510 0 L1021 410" stroke-width="1.2"/>
        <path d="M0 793 L510 1200 L1021 793" stroke-width="1.2"/>
        <path d="M0 0 L330 330 M1021 0 L690 330" stroke-width="0.8" opacity="0.6"/>
        <!-- main frames -->
        <rect x="80" y="65" width="865" height="1066" stroke-width="5"/>
        <rect x="108" y="87" width="810" height="1020" stroke-width="1.5"/>
        <!-- corner accents -->
        <path d="M150 0 V115 H0 M171 0 V95 H0" stroke-width="1.2"/>
        <path d="M861 0 V115 H1021 M850 0 V95 H1021" stroke-width="1.2"/>
        <path d="M150 1200 V1085 H0 M171 1200 V1105 H0" stroke-width="1.2"/>
        <path d="M861 1200 V1085 H1021 M850 1200 V1105 H1021" stroke-width="1.2"/>
      </g>
      <g fill="url(#goldStroke)">
        <circle cx="32" cy="24" r="9"/><circle cx="55" cy="42" r="4"/><circle cx="68" cy="54" r="3"/>
        <circle cx="989" cy="24" r="9"/><circle cx="966" cy="42" r="4"/><circle cx="953" cy="54" r="3"/>
        <circle cx="32" cy="1176" r="9"/><circle cx="55" cy="1158" r="4"/><circle cx="68" cy="1146" r="3"/>
        <circle cx="989" cy="1176" r="9"/><circle cx="966" cy="1158" r="4"/><circle cx="953" cy="1146" r="3"/>
      </g>
    </svg>

    <div class="gaming-art" role="img" aria-label="Four aces fanned over stacked black poker chips with two red dice"></div>

    <h1 class="title-casino">CASINO</h1>
    <div class="title-night">Night</div>

    <p class="event-date">THURSDAY 07TH, NOVEMBER 2019</p>
    <div class="rule rule-top"></div>
    <p class="venue">Venue : Copper Lantern Grill Johannesburg<br>Peltoni Vaal Plaza, 14 Orrin Lane, Sandton Arrive : 18: 30</p>
    <div class="rule rule-bottom"></div>
    <p class="details">Dress code : Smart Casual / Cocktail Entertainment<br>Drinks &amp; Snacks will be provided</p>

    <div class="rsvp">RSVP : Movent Representative</div>
  </main>
</body>
</html>
```